Business Card Design

New business card design

Target Market(s)

Residential & Commercial Property Managers

Industry/Entity Type

Plumbing Services

Contact Information for Business Card

Name - Rowan Keddle, title - Director, Phone Number - 0431 286 517, email - rowan@tbk-plumbing.com.au, Company ABN - 73 215 904 386,

Font styles to use
Sans Serif

Colors
0054AA
0677BA
7BADD7
CADEEF
E8F1F8

```html
<!DOCTYPE html>
<html lang="en">
<head>
<meta charset="utf-8">
<title>TBK Plumbing Services – Business Card</title>
<link rel="stylesheet" href="https://fonts.googleapis.com/css2?family=Montserrat:wght@400;500&family=Poppins:wght@700&display=swap">
<style>
  :root {
    --ink: #1f242b;
    --paper: #ffffff;
    --water: #12a3e3;
    --backdrop: #e8ecef;
    --muted: #6b6f75;
  }
  * { box-sizing: border-box; margin: 0; padding: 0; }
  html, body { width: 1200px; height: 895px; overflow: hidden; }
  body {
    background: var(--backdrop);
    font-family: "Montserrat", Arial, sans-serif;
    position: relative;
  }
  .card {
    position: absolute;
    top: 282px;
    width: 540px;
    height: 330px;
    border-radius: 22px;
    overflow: hidden;
    box-shadow: 0 10px 28px rgba(0,0,0,.18);
  }
  .card--back { left: 40px; background: var(--ink); }
  .card--front { left: 620px; background: var(--paper); }

  .wordmark {
    position: absolute;
    font-family: "Montserrat", Arial, sans-serif;
    font-weight: 500;
    letter-spacing: .06em;
    white-space: nowrap;
    display: flex;
    align-items: center;
    gap: 12px;
  }
  .wordmark__dot {
    width: 16px; height: 16px; border-radius: 50%;
    background: var(--water);
    flex: none;
  }
  .card--back .wordmark {
    left: 0; right: 0; top: 145px;
    justify-content: center;
    color: var(--paper);
    font-size: 30px;
  }
  .card--front .wordmark {
    left: 150px; top: 50px;
    color: var(--ink);
    font-size: 26px;
  }

  .person {
    position: absolute;
    right: 320px;
    top: 186px;
    text-align: right;
  }
  .person__name {
    font-family: "Poppins", Arial, sans-serif;
    font-weight: 700;
    font-size: 25px;
    color: var(--water);
    line-height: 1.1;
  }
  .person__title {
    font-size: 17px;
    color: var(--ink);
    margin-top: 2px;
  }
  .divider {
    position: absolute;
    left: 236px; top: 180px;
    width: 1px; height: 72px;
    background: var(--ink);
  }
  .contact {
    position: absolute;
    left: 252px; top: 184px;
    list-style: none;
    font-size: 14.5px;
    color: var(--ink);
  }
  .contact li { display: flex; align-items: center; gap: 8px; height: 26px; }
  .contact svg { width: 15px; height: 15px; flex: none; fill: var(--water); }

  .footer-band { position: absolute; left: 0; bottom: 0; width: 540px; height: 80px; }
  .abn {
    position: absolute;
    right: 26px; bottom: 24px;
    color: var(--paper);
    font-size: 14px;
    letter-spacing: .02em;
  }
</style>
</head>
<body>
  <section class="card card--back" aria-label="Card back">
    <div class="wordmark"><span class="wordmark__dot"></span>tbk plumbing services</div>
  </section>

  <section class="card card--front" aria-label="Card front">
    <div class="wordmark"><span class="wordmark__dot"></span>tbk plumbing services</div>

    <div class="person">
      <p class="person__name">Rowan Keddle</p>
      <p class="person__title">Director</p>
    </div>

    <div class="divider"></div>

    <ul class="contact">
      <li>
        <svg viewBox="0 0 24 24" aria-hidden="true"><path d="M6.6 10.8a15.1 15.1 0 0 0 6.6 6.6l2.2-2.2a1 1 0 0 1 1-.25 11.4 11.4 0 0 0 3.6.57 1 1 0 0 1 1 1V20a1 1 0 0 1-1 1A17 17 0 0 1 3 4a1 1 0 0 1 1-1h3.5a1 1 0 0 1 1 1c0 1.25.2 2.45.57 3.57a1 1 0 0 1-.25 1z"/></svg>
        0431 286 517
      </li>
      <li>
        <svg viewBox="0 0 24 24" aria-hidden="true"><path d="M2 5h20v14H2z M2 5l10 8 10-8" fill="var(--water)"/><path d="M3 6l9 7 9-7" fill="none" stroke="#fff" stroke-width="1.6"/></svg>
        rowan@tbk-plumbing.com.au
      </li>
    </ul>

    <svg class="footer-band" viewBox="0 0 540 80" aria-hidden="true">
      <polygon points="0,70 292,70 288,76 0,76" fill="var(--water)"/>
      <polygon points="300,80 312,40 540,40 540,80" fill="var(--ink)"/>
    </svg>
    <p class="abn">ABN - 73 215 904 386</p>
  </section>
</body>
</html>
```